Salon and Spa Distributor Business Card

Need a business card. We are are distributor in the salon and spa industry. We identify with natural beauty. Need a card with:
Company Name: Petal Quarry"
Title: "President & CEO"
Address
Company Phone number
email
website
Tag Line:" The Professional Salon Source"

Industry/Entity Type

Business

Contact Information for Business Card

Name: Dov Strommen
Title: "President & CEO"
Address: 31 Harlow Ln, Bexmoor, NJ 07813
Company Phone number: 800-463-5918
email: dovstrommen@petalquarry.example
website: www.petalquarry.example

Requirements
Should not have
• No black backgrounds

```html
<!DOCTYPE html>
<html lang="en">
<head>
<meta charset="utf-8">
<title>Petal Quarry Business Card</title>
<link href="https://fonts.googleapis.com/css2?family=Questrial&display=swap" rel="stylesheet">
<style>
  :root {
    --backdrop: #e4e4e4;
    --green-deep: #23783a;
    --green-mid: #4ea645;
    --green-bright: #66bb47;
    --green-text: #3f9a3c;
    --ink: #1c1c1c;
    --card-white: #ffffff;
  }
  * { margin: 0; padding: 0; box-sizing: border-box; }
  html, body {
    width: 1189px; height: 1200px; overflow: hidden;
    background: var(--backdrop);
    font-family: "Questrial", sans-serif;
  }
  .card {
    position: absolute; left: 171px; width: 856px; height: 487px;
    border-radius: 18px; overflow: hidden;
  }
  .card-front {
    top: 68px;
    background: radial-gradient(ellipse at 52% 40%, var(--green-bright) 0%, var(--green-mid) 45%, var(--green-deep) 100%);
  }
  .front-brand {
    position: absolute; left: 250px; top: 210px;
    display: flex; align-items: center; gap: 18px;
  }
  .brand-dot {
    width: 70px; height: 70px; border-radius: 50%;
    background: var(--card-white);
  }
  .front-name {
    color: var(--card-white); font-size: 57px; line-height: 1; letter-spacing: 0.5px;
  }
  .front-tagline {
    position: absolute; left: 338px; top: 284px;
    color: var(--card-white); font-size: 22px; letter-spacing: 1.6px;
  }
  .card-back { top: 626px; background: var(--card-white); }
  .back-art { position: absolute; left: 0; top: 0; width: 370px; height: 487px; }
  .back-info { position: absolute; left: 454px; top: 56px; color: var(--ink); }
  .back-name { color: var(--green-text); font-size: 50px; line-height: 1; }
  .back-tagline { font-size: 22px; margin-top: 6px; }
  .person-name { color: var(--green-text); font-size: 29px; margin-top: 70px; line-height: 1.1; }
  .person-title { font-size: 23px; line-height: 1.2; }
  .address { font-size: 23px; line-height: 1.25; margin-top: 28px; }
  .contact-list { list-style: none; margin-top: 14px; }
  .contact-list li {
    display: flex; align-items: center; gap: 10px;
    font-size: 22px; line-height: 28px;
  }
  .contact-icon { width: 22px; height: 22px; flex: none; }
</style>
</head>
<body>
  <section class="card card-front">
    <div class="front-brand">
      <span class="brand-dot"></span>
      <span class="front-name">Petal Quarry</span>
    </div>
    <p class="front-tagline">The Professional Salon Source</p>
  </section>

  <section class="card card-back">
    <svg class="back-art" role="img" aria-label="Large green brand artwork of flowing hair and leaves" viewBox="0 0 370 487">
      <defs>
        <linearGradient id="artGradient" x1="0" y1="0" x2="1" y2="1">
          <stop offset="0" stop-color="#5fb648"/>
          <stop offset="0.55" stop-color="#4da043"/>
          <stop offset="1" stop-color="#1f6f35"/>
        </linearGradient>
      </defs>
      <rect width="370" height="487" fill="url(#artGradient)"/>
    </svg>

    <div class="back-info">
      <h1 class="back-name">Petal Quarry</h1>
      <p class="back-tagline">The Professional Salon Source</p>
      <p class="person-name">Dov Strommen</p>
      <p class="person-title">President &amp; CEO</p>
      <p class="address">31 Harlow Ln,<br>Bexmoor, NJ 07813</p>
      <ul class="contact-list">
        <li>
          <svg class="contact-icon" viewBox="0 0 22 22" aria-hidden="true">
            <rect width="22" height="22" rx="3" fill="#3f9a3c"/>
            <path d="M5 8c0-2 3-3 6-3s6 1 6 3l-2 1-1-2H8L7 9z M7 10h8l1 6H6z" fill="#fff"/>
          </svg>
          <span>800-463-5918</span>
        </li>
        <li>
          <svg class="contact-icon" viewBox="0 0 22 22" aria-hidden="true">
            <rect width="22" height="22" rx="3" fill="#3f9a3c"/>
            <rect x="4" y="6" width="14" height="10" fill="none" stroke="#fff" stroke-width="1.5"/>
            <path d="M4 6l7 6 7-6" fill="none" stroke="#fff" stroke-width="1.5"/>
          </svg>
          <span>dovstrommen@petalquarry.example</span>
        </li>
        <li>
          <svg class="contact-icon" viewBox="0 0 22 22" aria-hidden="true">
            <rect width="22" height="22" rx="3" fill="#3f9a3c"/>
            <circle cx="11" cy="11" r="6.5" fill="none" stroke="#fff" stroke-width="1.3"/>
            <ellipse cx="11" cy="11" rx="3" ry="6.5" fill="none" stroke="#fff" stroke-width="1.1"/>
            <path d="M4.5 11h13M6 7.5h10M6 14.5h10" stroke="#fff" stroke-width="1.1"/>
          </svg>
          <span>www.petalquarry.example</span>
        </li>
      </ul>
    </div>
  </section>
</body>
</html>
```